Shine Fox Auto Care Business Card

2 side business card design for an auto detailing business

Target Market(s)

Auto detailing

Contact Information for Business Card

Things included

The business name “Shine Fox Auto Care”
Mark Dunrow
(403)271-6094
Marlow Falls, Sk

Services offered - complete interior& exterior detail
- paint correction & protection
- ceramic coating
- trim restore
- auto carpet & seat cleaning

Requirements
Must have
• Colours that are in my logo

Services offered

My name Mark Dunrow
403-271-6094
Marlow Falls, Sk

Not too sure in what order for these ?
Website. Shinefoxautocare.com
Instagram Shinefoxautocare
Email. Shinefoxautoac@mailvento.com

```html
<!DOCTYPE html>
<html lang="en">
<head>
<meta charset="utf-8">
<title>Shine Fox Auto Care – Business Card</title>
<link href="https://fonts.googleapis.com/css2?family=Arimo:wght@400;700&display=swap" rel="stylesheet">
<style>
  :root {
    --page: #2a2624;
    --card: #000000;
    --red: #9b0a0f;
    --red-text: #b3121a;
    --white: #ffffff;
    --rule: #5a5a5a;
  }
  * { margin: 0; padding: 0; box-sizing: border-box; }
  html, body { width: 1200px; height: 842px; overflow: hidden; }
  body {
    background: var(--page);
    font-family: "Arimo", Arial, sans-serif;
    display: flex;
    align-items: center;
    justify-content: center;
    gap: 40px;
  }
  .card {
    position: relative;
    width: 520px;
    height: 298px;
    background: var(--card);
    color: var(--white);
    box-shadow: 0 10px 30px rgba(0,0,0,.5);
    overflow: hidden;
  }
  .band { position: absolute; left: 0; right: 0; height: 14px; background: var(--red); }
  .band--top { top: 0; }
  .band--bottom { bottom: 0; }

  /* contact side */
  .contact { display: flex; flex-direction: column; align-items: center; padding-top: 64px; text-align: center; }
  .contact__name { color: var(--red-text); font-size: 24px; letter-spacing: 1px; text-transform: uppercase; font-weight: 400; }
  .divider { display: flex; align-items: center; gap: 6px; width: 300px; margin: 6px 0 8px; }
  .divider__rule { flex: 1; height: 1px; background: var(--rule); }
  .icon { width: 22px; height: 22px; }
  .contact__line { font-size: 15px; line-height: 19px; }
  .contact__place { font-size: 17px; margin-top: 2px; }

  /* brand side */
  .brand { display: flex; flex-direction: column; align-items: center; padding-top: 36px; }
  .brand__mark { width: 62px; height: 62px; border-radius: 50%; border: 8px solid var(--red); margin-bottom: 12px; }
  .brand__name { font-size: 34px; font-weight: 700; letter-spacing: 2px; text-transform: uppercase; line-height: 1; }
  .brand__sub { font-size: 34px; font-weight: 700; letter-spacing: 2px; text-transform: uppercase; line-height: 1.1; }
  .brand__tagline { color: var(--red-text); font-size: 11px; text-transform: uppercase; margin: 10px 0 10px; letter-spacing: .3px; }
  .services { list-style: none; display: grid; grid-template-columns: auto auto; column-gap: 26px; row-gap: 3px; font-size: 13px; }
  .services li { display: flex; align-items: center; gap: 6px; }
  .services li::before { content: ""; width: 9px; height: 9px; border-radius: 50%; border: 1.5px solid var(--red-text); }
</style>
</head>
<body>

<section class="card card--contact">
  <div class="band band--top"></div>
  <div class="contact">
    <h1 class="contact__name">Mark Dunrow</h1>
    <div class="divider">
      <span class="divider__rule"></span>
      <svg class="icon" viewBox="0 0 24 24" aria-label="phone"><circle cx="12" cy="12" r="11" fill="none" stroke="#9b0a0f" stroke-width="1.5"/><path d="M8 6l2 0 1 3-1.5 1.2a7 7 0 0 0 4.3 4.3L15 13l3 1v2a1.5 1.5 0 0 1-1.5 1.5A10 10 0 0 1 6.5 7.5 1.5 1.5 0 0 1 8 6z" fill="#9b0a0f"/></svg>
      <svg class="icon" viewBox="0 0 24 24" aria-label="email"><circle cx="12" cy="12" r="11" fill="none" stroke="#9b0a0f" stroke-width="1.5"/><rect x="6" y="8" width="12" height="8" fill="#9b0a0f"/><path d="M6 8l6 5 6-5" fill="none" stroke="#000" stroke-width="1"/></svg>
      <svg class="icon" viewBox="0 0 24 24" aria-label="website"><circle cx="12" cy="12" r="11" fill="none" stroke="#9b0a0f" stroke-width="1.5"/><circle cx="12" cy="12" r="6" fill="none" stroke="#9b0a0f" stroke-width="1.5"/><path d="M6 12h12M12 6c-3 3-3 9 0 12M12 6c3 3 3 9 0 12" fill="none" stroke="#9b0a0f" stroke-width="1.2"/></svg>
      <span class="divider__rule"></span>
    </div>
    <p class="contact__line">(403)271-6094</p>
    <p class="contact__line">Shinefoxautocare@mailvento.com</p>
    <p class="contact__line">www.Shinefoxautocare.com</p>
    <div class="divider">
      <span class="divider__rule"></span>
      <svg class="icon" viewBox="0 0 24 24" aria-label="location"><circle cx="12" cy="12" r="11" fill="none" stroke="#9b0a0f" stroke-width="1.5"/><path d="M12 5a4.5 4.5 0 0 0-4.5 4.5c0 3.5 4.5 9 4.5 9s4.5-5.5 4.5-9A4.5 4.5 0 0 0 12 5z" fill="#9b0a0f"/><circle cx="12" cy="9.5" r="1.6" fill="#000"/></svg>
      <span class="divider__rule"></span>
    </div>
    <p class="contact__place">Marlow Falls, Sk</p>
  </div>
  <div class="band band--bottom"></div>
</section>

<section class="card card--brand">
  <div class="band band--top"></div>
  <div class="brand">
    <div class="brand__mark"></div>
    <h2 class="brand__name">Shine Fox</h2>
    <p class="brand__sub">Auto Care</p>
    <p class="brand__tagline">Complete interior &amp; exterior detail</p>
    <ul class="services">
      <li>Paint correction &amp; protection</li>
      <li>Ceramic coating</li>
      <li>Auto carpet &amp; seat cleaning</li>
      <li>Trim restore</li>
    </ul>
  </div>
  <div class="band band--bottom"></div>
</section>

</body>
</html>
```